Varnor Immigration _Cloud-based, boutique law firm serving clients worldwide in US Immigration Law

I need a website for my new US immigration law firm that will be based in Montreal, QC Canada but serve clients worldwide to achieve their US immigration goals. This will be a boutique firm offering attentive and compassionate service to our corporate and individual clients. I'd like the site to be fresh, modern, sophisticated and easy to read.

I will need a home page, about/bio page, services page, and contact me page with a form so potential clients could email inquiries and also schedule consultations. I would also like a 'Book a Consultation' button on the home page (easily visible).

The longest website page is going to be the 'Services' tab, which I'd like to break down to services for Employers and services Individuals, with further sub-sets of services to each type of client. I envision images with short text that display longer text when hoovering over.

To start, I would have 3 subsets of services for Employers and 5 subsets of services for Individuals. I will need the ability to expand/edit these pages in Wix interface as we grow.

The site will need to be in English and in French.

I like the color blue and the final design should communicate the firm's core values: integrity and compassion. In other words, we do right, no matter what and are understanding to individual circumstances. I'd like the site to convey sophistication and accessibility. I don't like staged stock photos of people. Sites with a lot of stock photos of people feels unauthentic to me.

Logo draft is attached in jpeg. Navy and gold colors.
Example of 4 law firm sites I like below:
- https://www.quilbanelaw.example/
-https://www.zetrivlaw.example/
-https://harlowinappeals.example/
-https://www.ombrekilaw.example/

Target Market(s)

Small-medium sized businesses (10-999 employees) in US with foreign workforce; Foreign entrepreneurs wishing to implant in the US

Industry/Entity Type

Law

Coding

Font styles to use
Sans Serif

Colors

Designer to choose colors to be used in the design.

Requirements
Must have
• Great Home Page (Grabs attention with eye-catching images/text; Immediately establishes credibility; Provides an overview of services; Encourages visitor to take the next action.)
Nice to have
• Images of Montreal (where firm is based); Images of bridges (symbolizes progress, movement, connections)
Should not have
• Non-authentic photos: staged people at desks or pictures of court buildings.

```html
<!DOCTYPE html>
<html lang="en">
<head>
<meta charset="utf-8">
<title>Varnor Immigration</title>
<link href="https://fonts.googleapis.com/css2?family=Libre+Caslon+Text&family=Roboto:wght@400;500;700&display=swap" rel="stylesheet">
<style>
:root{
  --navy:#343a55;
  --navy-deep:#2d3350;
  --gold-light:#e6d3a0;
  --gold:#c9a35e;
  --gold-dark:#b98d3f;
  --ink:#222;
  --text:#666;
  --muted-bg:#f4f4f4;
  --white:#fff;
  --frame:#7b7566;
}
*{margin:0;padding:0;box-sizing:border-box}
html,body{width:1200px;height:3842px;overflow:hidden}
body{position:relative;font-family:'Roboto',sans-serif;color:var(--text);background:var(--white)}
.abs{position:absolute}
.serif{font-family:'Libre Caslon Text',serif;font-weight:400}
.gold-grad{background:linear-gradient(180deg,var(--gold-light),var(--gold-dark))}
.btn{position:absolute;display:flex;align-items:center;justify-content:center;color:var(--white);font-size:14px;font-weight:700;text-transform:uppercase;letter-spacing:.2px}

/* header */
.site-header{left:0;top:0;width:1200px;height:85px;background:var(--navy)}
.brand-mark{left:104px;top:10px;width:60px;height:60px;border-radius:50%;background:#6b6a67;border:2px solid #8c8570}
.brand-name{left:172px;top:8px;width:210px;font-size:21px;line-height:25px;letter-spacing:3px;color:#b9b3a2;text-transform:uppercase}
.brand-tag{left:173px;top:60px;font-size:9px;letter-spacing:2px;color:#b9b3a2;text-transform:uppercase}
.nav a{position:absolute;top:32px;font-size:14px;color:var(--white);text-decoration:none}
.nav a.active{color:var(--gold)}
.nav .underline{position:absolute;left:422px;top:81px;width:42px;height:4px;background:var(--gold)}
.lang-flag{left:778px;top:25px;width:30px;height:30px;border-radius:50%;background:linear-gradient(180deg,#c63b45 0 50%,#f1f1f1 50% 100%)}
.lang-flag::before{content:"";position:absolute;left:0;top:0;width:15px;height:15px;background:#2f4c8f;border-top-left-radius:15px}
.call-box{left:879px;top:0;width:321px;height:85px}
.call-icon{left:33px;top:22px;width:42px;height:42px;border-radius:50%;border:2px solid var(--white)}
.call-label{left:89px;top:22px;font-size:13px;color:var(--white)}
.call-number{left:89px;top:40px;font-size:21px;font-weight:700;color:var(--white)}

/* hero */
.hero{left:0;top:85px;width:1200px;height:685px;background:linear-gradient(180deg,#3e6fb0 0%,#8fb3d6 30%,#6b7f87 55%,#3d5a35 80%,#55604a 100%)}
.hero-title{left:104px;top:115px;width:520px;font-size:54px;line-height:61px;color:var(--white);text-transform:uppercase}
.hero .btn{left:109px;top:436px;width:204px;height:42px}
.slider-line{left:0;top:627px;width:92px;height:2px;background:var(--white)}
.dot{width:30px;height:30px;border-radius:50%;top:612px;display:flex;align-items:center;justify-content:center;font-size:13px;font-weight:700;color:var(--white);background:var(--navy)}
.dot.on{background:var(--white);color:var(--navy)}

/* about */
.section-title{font-size:38px;color:var(--ink);text-transform:uppercase}
.about-title{left:109px;top:866px}
.about-text{left:110px;width:479px;font-size:14px;line-height:25.6px;text-align:justify}
.about .btn{left:109px;top:1237px;width:137px;height:42px}
.portrait-frame{left:928px;top:873px;width:160px;height:406px}
.portrait{left:636px;top:894px;width:427px;height:365px;background:linear-gradient(135deg,#2a2d33,#4a5670 55%,#6a87a8)}

/* services */
.services{left:0;top:1383px;width:1200px;height:891px;background:var(--muted-bg)}
.services-title{left:0;top:96px;width:1200px;text-align:center}
.card{width:307px;height:294px;background:var(--white);box-shadow:0 1px 4px rgba(0,0,0,.08)}
.card svg.icon{position:absolute;left:42px;top:22px;width:88px;height:88px;fill:none;stroke:#6f6a60;stroke-width:2}
.card .pointer{position:absolute;left:0;top:134px;width:0;height:0;border-top:9px solid transparent;border-bottom:9px solid transparent;border-left:18px solid #8b8578}
.card h3{position:absolute;left:40px;top:130px;font-size:21px;font-weight:500;color:var(--ink)}
.card p{position:absolute;left:40px;top:168px;width:245px;font-size:14px;line-height:25.6px}
.card.featured{background:linear-gradient(180deg,var(--gold-light),var(--gold-dark))}
.card.featured h3,.card.featured p{color:var(--white)}
.card.featured svg.icon{stroke:var(--white)}
.card.featured .pointer{border-left-color:var(--white)}

/* testimonials */
.testimonials-title{left:0;top:2366px;width:1200px;text-align:center}
.quote-box{width:487px;height:269px}
.quote-box .frame{position:absolute;border:2px solid var(--frame)}
.quote-box .f1{left:0;top:0;width:481px;height:263px}
.quote-box .f2{left:6px;top:6px;width:481px;height:263px}
.quote-mark{position:absolute;left:34px;top:-40px;font-family:'Libre Caslon Text',serif;font-size:110px;line-height:110px;color:var(--gold);background:var(--white);padding:0 6px;height:62px;overflow:hidden}
.quote-box p{position:absolute;left:39px;top:64px;width:410px;font-size:14px;line-height:25.6px}
.quote-box h4{position:absolute;left:39px;top:184px;font-size:21px;font-weight:500;color:var(--ink)}
.quote-box span{position:absolute;left:39px;top:214px;font-size:14px}

/* consultation */
.city-band{left:0;top:2844px;width:1200px;height:487px;background:linear-gradient(180deg,#6f7380 0%,#c79a6a 35%,#7a6a66 55%,#3a3b48 100%)}
.footer-left{left:0;top:3331px;width:390px;height:511px;background:var(--navy)}
.consult{left:599px;top:2917px;width:489px;height:492px}
.consult .lead{position:absolute;left:0;top:28px;width:489px;text-align:center;font-size:20px;color:var(--white);text-transform:uppercase}
.consult .headline{position:absolute;left:0;top:72px;width:489px;text-align:center;font-size:30px;color:var(--navy);text-transform:uppercase}
.field{position:absolute;left:45px;width:402px;height:40px;background:var(--white);font-size:13px;color:#555;padding:12px 15px}
.submit{left:45px;top:418px;width:402px;height:40px;background:var(--navy)}

/* footer */
.foot-mark{left:80px;top:3490px;width:56px;height:56px;border-radius:50%;background:#6b6a67;border:2px solid #8c8570}
.foot-name{left:144px;top:3492px;width:200px;font-size:19px;line-height:24px;letter-spacing:3px;color:#b9b3a2;text-transform:uppercase}
.foot-tag{left:145px;top:3542px;font-size:8px;letter-spacing:2px;color:#b9b3a2;text-transform:uppercase}
.foot-about{left:77px;top:3572px;width:262px;font-size:14px;line-height:25.8px;color:var(--white)}
.foot-head{font-size:21px;font-weight:400;color:var(--ink)}
.foot-rule{width:45px;height:2px;background:#8b8578}
.quick-links{left:454px;top:3545px;list-style:none}
.quick-links li{font-size:14px;line-height:25.8px;padding-left:26px;position:relative}
.quick-links li::before{content:"";position:absolute;left:0;top:10px;width:6px;height:6px;background:#777}
.contact-row{left:669px;font-size:14px;line-height:25.8px}
.contact-row svg{position:absolute;left:0;top:5px;width:14px;height:14px;fill:#888}
.contact-row span{display:block;padding-left:25px}
.login{left:946px;top:3485px;width:143px;height:40px}
.register{left:946px;top:3536px;width:143px;height:40px;background:var(--navy)}
.follow{left:949px;top:3615px;font-size:14px;font-weight:700;color:var(--ink)}
.social{width:33px;height:33px;top:3643px;background:#eee}
.social::after{content:"";position:absolute;left:13px;top:13px;width:7px;height:7px;background:#555}
.copyright{left:0;top:3772px;width:1200px;text-align:center;font-size:13px;color:#444;padding-left:290px}
</style>
</head>
<body>

<header class="abs site-header">
  <div class="abs brand-mark"></div>
  <div class="abs brand-name serif">Varnor Immigration</div>
  <div class="abs brand-tag serif">Elise Varnor, Attorney</div>
  <nav class="nav">
    <a class="active" style="left:422px">HOME</a>
    <a style="left:484px">ABOUT US</a>
    <a style="left:574px">SERVICES</a>
    <a style="left:662px">CONTACT US</a>
    <span class="underline"></span>
  </nav>
  <div class="abs lang-flag" role="img" aria-label="English language flag"></div>
  <div class="abs" style="left:816px;top:32px;font-size:14px;color:#fff">ENG &#8964;</div>
  <div class="abs call-box gold-grad">
    <div class="abs call-icon">
      <svg viewBox="0 0 24 24" width="20" height="20" style="position:absolute;left:9px;top:9px"><path d="M6.6 10.8a15 15 0 0 0 6.6 6.6l2.2-2.2c.3-.3.7-.4 1-.2 1.1.4 2.3.6 3.6.6.6 0 1 .4 1 1V20c0 .6-.4 1-1 1A17 17 0 0 1 3 4c0-.6.4-1 1-1h3.5c.6 0 1 .4 1 1 0 1.3.2 2.5.6 3.6.1.3 0 .7-.2 1z" fill="none" stroke="#fff" stroke-width="1.6"/></svg>
    </div>
    <div class="abs call-label">CALL US TODAY :</div>
    <div class="abs call-number">+1 888 888 8888</div>
  </div>
</header>

<section class="abs hero" role="img" aria-label="Aerial photo of downtown Montreal skyline with cathedral dome and green park">
  <h1 class="abs hero-title serif">Serve clients worldwide to achieve their US immigration goals</h1>
  <a class="btn gold-grad">Book a consultation</a>
  <div class="abs slider-line"></div>
  <div class="abs dot on" style="left:112px">1</div>
  <div class="abs dot" style="left:146px">2</div>
  <div class="abs dot" style="left:180px">3</div>
</section>

<section class="about">
  <h2 class="abs section-title serif about-title">About me</h2>
  <p class="abs about-text" style="top:930px">Lorem ipsum dolor sit amet, consectetur adipiscing elit, sed do eiusmod tempor incididunt ut labore et dolore magna aliqua. Ut enim ad minim veniam, quis nostrud exercitation ullamco laboris nisi ut aliquip ex ea commodo consequat. Duis aute irure dolor in reprehenderit in voluptate velit esse cillum dolore eu fugiat nulla pariatur.</p>
  <p class="abs about-text" style="top:1084px">Excepteur sint occaecat cupidatat non proident, sunt in culpa qui officia deserunt mollit anim id est laborum. Lorem ipsum dolor sit amet, consectetur adipiscing elit, sed do eiusmod tempor incididunt ut labore et dolore magna aliqua. Excepteur sint occaecat cupidatat non proident, sunt in culpa qui officia deserunt Excepteur sint occaecat</p>
  <a class="btn gold-grad" style="left:109px;top:1237px;width:137px;height:42px">Learn more</a>
  <div class="abs portrait-frame gold-grad"></div>
  <div class="abs portrait" role="img" aria-label="Portrait of the attorney in a blue blouse in front of a night city view"></div>
</section>

<section class="abs services">
  <h2 class="abs section-title serif services-title">Our services</h2>

  <article class="abs card" style="left:112px;top:168px">
    <svg class="icon" viewBox="0 0 88 88"><circle cx="46" cy="46" r="26"/><ellipse cx="46" cy="46" rx="12" ry="26"/><path d="M20 46h52M24 33h44M24 59h44"/><circle cx="14" cy="10" r="6"/><path d="M4 26a10 10 0 0 1 20 0z"/><circle cx="76" cy="70" r="6"/><path d="M66 86a10 10 0 0 1 20 0z"/></svg>
    <span class="pointer"></span>
    <h3>Duis aute irure dolor</h3>
    <p>Lorem ipsum dolor sit amet, consec tetur adipiscing elit, sed do eiusmod tempor incididunt ut labore et dolore magna aliqua.</p>
  </article>
  <article class="abs card featured" style="left:447px;top:168px">
    <svg class="icon" viewBox="0 0 88 88"><rect x="22" y="8" width="52" height="70"/><path d="M28 14h40v58H28"/><circle cx="56" cy="30" r="9"/><path d="M47 30h18M56 21v18M36 50h30M36 58h30M36 66h20"/><circle cx="14" cy="36" r="6"/><path d="M4 78V54a10 10 0 0 1 20 0v24"/></svg>
    <span class="pointer"></span>
    <h3>Duis aute irure dolor</h3>
    <p>Lorem ipsum dolor sit amet, consec tetur adipiscing elit, sed do eiusmod tempor incididunt ut labore et dolore magna aliqua.</p>
  </article>
  <article class="abs card" style="left:781px;top:168px">
    <svg class="icon" viewBox="0 0 88 88"><path d="M44 78S24 56 24 40a20 20 0 0 1 40 0c0 16-20 38-20 38z"/><circle cx="44" cy="36" r="8"/><path d="M32 54a12 12 0 0 1 24 0"/><path d="M6 6l14 14M6 6h10M6 6v10M82 6L68 20M82 6H72M82 6v10M6 82l14-14M6 82h10M6 82V72M82 82L68 68M82 82H72M82 82V72"/></svg>
    <span class="pointer"></span>
    <h3>Duis aute irure dolor</h3>
    <p>Lorem ipsum dolor sit amet, consec tetur adipiscing elit, sed do eiusmod tempor incididunt ut labore et dolore magna aliqua.</p>
  </article>

  <article class="abs card" style="left:112px;top:493px">
    <svg class="icon" viewBox="0 0 88 88"><path d="M20 30a12 12 0 0 1 8-20 16 16 0 0 1 30 4 10 10 0 0 1 2 20H22"/><path d="M40 34v10"/><rect x="4" y="46" width="28" height="8" rx="3"/><rect x="4" y="56" width="28" height="8" rx="3"/><rect x="4" y="66" width="28" height="8" rx="3"/><rect x="4" y="76" width="28" height="8" rx="3"/><circle cx="60" cy="66" r="16"/><circle cx="60" cy="62" r="5"/><path d="M51 78a9 9 0 0 1 18 0"/></svg>
    <span class="pointer"></span>
    <h3>Duis aute irure dolor</h3>
    <p>Lorem ipsum dolor sit amet, consec tetur adipiscing elit, sed do eiusmod tempor incididunt ut labore et dolore magna aliqua.</p>
  </article>
  <article class="abs card" style="left:447px;top:493px">
    <svg class="icon" viewBox="0 0 88 88"><path d="M40 30a12 12 0 0 1 10-20 16 16 0 0 1 30 6 10 10 0 0 1-2 20H44"/><circle cx="62" cy="26" r="7"/><circle cx="28" cy="46" r="9"/><path d="M10 84V70a18 18 0 0 1 36 0v14z"/><path d="M46 62c6-2 10-8 10-16"/><path d="M52 50l4-6 4 6"/></svg>
    <span class="pointer"></span>
    <h3>Duis aute irure dolor</h3>
    <p>Lorem ipsum dolor sit amet, consec tetur adipiscing elit, sed do eiusmod tempor incididunt ut labore et dolore magna aliqua.</p>
  </article>
  <article class="abs card" style="left:781px;top:493px">
    <svg class="icon" viewBox="0 0 88 88"><rect x="12" y="10" width="64" height="72"/><path d="M12 22h64M18 10V4h52v6M24 34v40M36 34v40M52 34v40M64 34v40M38 82V58h12v24"/></svg>
    <span class="pointer"></span>
    <h3>Duis aute irure dolor</h3>
    <p>Lorem ipsum dolor sit amet, consec tetur adipiscing elit, sed do eiusmod tempor incididunt ut labore et dolore magna aliqua.</p>
  </article>
</section>

<section class="testimonials">
  <h2 class="abs section-title serif testimonials-title">Testimonials</h2>
  <figure class="abs quote-box" style="left:100px;top:2473px">
    <span class="frame f1"></span><span class="frame f2"></span>
    <span class="quote-mark">&ldquo;</span>
    <p>Lorem ipsum dolor sit amet, consectetur adipiscing elit, sed do eiusmod tempor incididunt ut labore et dolore magna aliqua. Ut enim ad minim veniam, quis nostrud exercitation ullamco laboris nisi ut aliquip ex ea commodo consequat.</p>
    <h4>John Doe</h4>
    <span>Company name</span>
  </figure>
  <figure class="abs quote-box" style="left:611px;top:2473px">
    <span class="frame f1"></span><span class="frame f2"></span>
    <span class="quote-mark">&ldquo;</span>
    <p>Lorem ipsum dolor sit amet, consectetur adipiscing elit, sed do eiusmod tempor incididunt ut labore et dolore magna aliqua. Ut enim ad minim veniam, quis nostrud exercitation ullamco laboris nisi ut aliquip ex ea commodo consequat.</p>
    <h4>John Doe</h4>
    <span>Company name</span>
  </figure>
</section>

<div class="abs city-band" role="img" aria-label="Montreal skyline at sunset with dramatic clouds"></div>
<div class="abs footer-left"></div>

<section class="abs consult gold-grad">
  <div class="lead">Let us start helping you with a</div>
  <div class="headline serif">Free consultation</div>
  <div class="field" style="top:120px">Name</div>
  <div class="field" style="top:173px">Email</div>
  <div class="field" style="top:228px">Phone</div>
  <div class="field" style="top:282px;height:119px">Message</div>
  <div class="btn submit">Submit</div>
</section>

<footer>
  <div class="abs foot-mark"></div>
  <div class="abs foot-name serif">Varnor Immigration</div>
  <div class="abs foot-tag serif">Elise Varnor, Attorney</div>
  <p class="abs foot-about">Lorem ipsum dolor sit amet, conse ctet ur adipiscing elit, sed do eiusmod temp or incididunt ut labore et dolore magna aliqua. Ut enim ad minim veniam, quis nostrud exercitation</p>

  <h4 class="abs foot-head" style="left:454px;top:3478px">Quick links</h4>
  <div class="abs foot-rule" style="left:454px;top:3524px"></div>
  <ul class="abs quick-links">
    <li>Home</li><li>About us</li><li>Services</li><li>Testimonials</li><li>Blog</li><li>Contact us</li>
  </ul>

  <h4 class="abs foot-head" style="left:669px;top:3478px">Contact us</h4>
  <div class="abs foot-rule" style="left:669px;top:3524px"></div>
  <div class="abs contact-row" style="top:3545px;width:230px">
    <svg viewBox="0 0 24 24"><path d="M12 2a7 7 0 0 0-7 7c0 5 7 13 7 13s7-8 7-13a7 7 0 0 0-7-7zm0 9.5A2.5 2.5 0 1 1 12 6.5a2.5 2.5 0 0 1 0 5z"/></svg>
    <span>Lorem ipsum dolor sit amet, consectetur</span>
  </div>
  <div class="abs contact-row" style="top:3622px">
    <svg viewBox="0 0 24 24"><path d="M6.6 10.8a15 15 0 0 0 6.6 6.6l2.2-2.2c.3-.3.7-.4 1-.2 1.1.4 2.3.6 3.6.6.6 0 1 .4 1 1V20c0 .6-.4 1-1 1A17 17 0 0 1 3 4c0-.6.4-1 1-1h3.5c.6 0 1 .4 1 1 0 1.3.2 2.5.6 3.6.1.3 0 .7-.2 1z"/></svg>
    <span>+1 888 888 8888</span>
  </div>
  <div class="abs contact-row" style="top:3673px">
    <svg viewBox="0 0 24 24"><path d="M2 5h20v14H2zm2 2v.5l8 5 8-5V7z"/></svg>
    <span>info@companyname.com</span>
  </div>

  <a class="btn gold-grad login">Login</a>
  <a class="btn register">Register</a>
  <div class="abs follow">FOLLOW US :</div>
  <span class="abs social" style="left:949px" aria-label="Social link"></span>
  <span class="abs social" style="left:989px" aria-label="Social link"></span>
  <span class="abs social" style="left:1029px" aria-label="Social link"></span>
  <span class="abs social" style="left:1069px" aria-label="Social link"></span>

  <div class="abs copyright">&copy; Copyrights Company name 2023. All rights reserved | Privacy policy | Terms Condition</div>
</footer>

</body>
</html>
```